Upscale business cards needed for Board of Directors

We need professional business cards created for members of our family business Board of Directors. We would like these relatively simple and straightforward, but also with a unique element to set them apart. Probably stick with neutral and simple colors - white, grey etc. We need space for the traditional elements, including name, title, address, email/phone number. And we will be creating several from this template so it needs to be template that is easy to switch information in and out of.
Business
See description

```html
<!DOCTYPE html>
<html lang="en">
<head>
<meta charset="utf-8">
<title>Corwin Holdings – Business Card</title>
<link href="https://fonts.googleapis.com/css2?family=Roboto:wght@400;500;700&display=swap" rel="stylesheet">
<style>
  :root {
    --backdrop: #3a3a3c;
    --gold: #b9a57e;
    --gold-light: #cbb994;
    --gold-dark: #a48f66;
    --ink: #1f1f1f;
    --text-grey: #6b6b6b;
    --paper: #ffffff;
    --band: #1c1c1c;
    --logo-light: #f4f4f2;
  }
  * { box-sizing: border-box; margin: 0; padding: 0; }
  html, body {
    width: 1200px; height: 843px; overflow: hidden;
    background: var(--backdrop);
    font-family: "Roboto", Arial, sans-serif;
  }
  .canvas { position: relative; width: 1200px; height: 843px; }
  .card {
    position: absolute; left: 320px; width: 560px; height: 320px;
    box-shadow: 0 10px 28px rgba(0,0,0,0.45);
    overflow: hidden;
  }
  /* Back side */
  .card-back {
    top: 80px;
    background: linear-gradient(120deg, var(--gold-dark), var(--gold-light) 55%, var(--gold));
    display: flex; align-items: center; justify-content: center;
  }
  .brand {
    color: var(--logo-light); font-weight: 700; text-transform: uppercase;
    text-align: center; line-height: 1; white-space: nowrap;
  }
  .brand-name { display: block; font-size: 58px; letter-spacing: 1px; }
  .brand-sub { display: block; font-size: 24px; letter-spacing: 12px; margin-top: 6px; padding-left: 12px; }

  /* Front side */
  .card-front { top: 440px; background: var(--paper); display: flex; }
  .details { position: relative; flex: 1; }
  .icon-column { position: absolute; left: 36px; top: 0; height: 100%; width: 20px; }
  .icon { position: absolute; left: 0; width: 16px; height: 16px; fill: var(--ink); }
  .divider {
    position: absolute; left: 72px; top: 28px; width: 3px; height: 262px;
    background: var(--gold);
  }
  .info { position: absolute; left: 96px; top: 0; width: 300px; }
  .person-name {
    position: absolute; top: 34px; font-size: 22px; font-weight: 500;
    color: var(--ink); letter-spacing: 1px; text-transform: uppercase; white-space: nowrap;
  }
  .person-title { position: absolute; top: 62px; font-size: 16px; color: var(--gold); }
  .address, .contacts {
    position: absolute; font-size: 16px; color: var(--text-grey); line-height: 1.4; white-space: nowrap;
  }
  .address { top: 108px; }
  .contacts { top: 196px; }

  .band { position: relative; width: 168px; background: var(--band); }
  .band-rule {
    position: absolute; left: 34px; top: 30px; width: 3px; height: 260px;
    background: var(--gold);
  }
  .band-brand {
    position: absolute; left: 50%; top: 50%; width: 290px;
    transform: translate(-50%, -50%) rotate(-90deg);
  }
  .band-brand .brand-name { font-size: 46px; }
  .band-brand .brand-sub { font-size: 20px; letter-spacing: 9px; padding-left: 9px; margin-top: 6px; }
</style>
</head>
<body>
<main class="canvas">
  <section class="card card-back" aria-label="Card back">
    <div class="brand">
      <span class="brand-name">Corwin</span>
      <span class="brand-sub">Holdings</span>
    </div>
  </section>

  <section class="card card-front" aria-label="Card front">
    <div class="details">
      <div class="icon-column">
        <svg class="icon" style="top:38px" viewBox="0 0 16 16" aria-hidden="true"><circle cx="8" cy="5" r="3.5"/><path d="M1.5 15c0-4 3-6 6.5-6s6.5 2 6.5 6z"/></svg>
        <svg class="icon" style="top:112px" viewBox="0 0 16 16" aria-hidden="true"><path d="M8 0.5a5 5 0 0 0-5 5c0 3.8 5 10 5 10s5-6.2 5-10a5 5 0 0 0-5-5zm0 7a2 2 0 1 1 0-4 2 2 0 0 1 0 4z"/></svg>
        <svg class="icon" style="top:198px" viewBox="0 0 16 16" aria-hidden="true"><path d="M3.5 1l2.5 0.3 1 3-1.6 1.3a9 9 0 0 0 5 5l1.3-1.6 3 1 .3 2.5c-.5 1.5-2 2-3 2A12 12 0 0 1 1.5 4c0-1 .5-2.5 2-3z"/></svg>
        <svg class="icon" style="top:221px" viewBox="0 0 16 16" aria-hidden="true"><path d="M1 3h14v10H1z M1.6 3.6L8 8.8l6.4-5.2" stroke="#fff" stroke-width="1.2"/></svg>
        <svg class="icon" style="top:244px" viewBox="0 0 16 16" aria-hidden="true"><circle cx="8" cy="8" r="7"/><path d="M1 8h14M8 1c2.5 2.5 2.5 11.5 0 14M8 1c-2.5 2.5-2.5 11.5 0 14" stroke="#fff" stroke-width="1" fill="none"/></svg>
      </div>
      <div class="divider"></div>
      <div class="info">
        <p class="person-name">Marcus Hale</p>
        <p class="person-title">President</p>
        <p class="address">412 Alder Crest Lane<br>Glen Harbor, NY 11702</p>
        <p class="contacts">555 0142 7730<br>marcus@example.com<br>www.example.com</p>
      </div>
    </div>
    <div class="band">
      <div class="band-rule"></div>
      <div class="brand band-brand">
        <span class="brand-name">Corwin</span>
        <span class="brand-sub">Holdings</span>
      </div>
    </div>
  </section>
</main>
</body>
</html>
```